Marlowe Group needs a business card

I would like the card to be simple but modern and elegant.
I like black and white.
or black and gold.
we are a private finance lender and also are involved in property and property developments.

please look at the business card photos i provided i would like M.G only one one side and all the other details on the other side use fonts that tie in with my theme.

Industry/Entity Type

Finance

Contact Information for Business Card

Marlowe Group (M.G) Daniel Marlowe M: 0413586207 E: danmarl@inboxmail.test

Font styles to use
Other font styles liked:
• Use fonts that would reflect our business

Colors
000000
ffffff

Requirements
Must have
• one side of details
• other side has either M.G or Marlowe Group like in the photos provided

```html
<!DOCTYPE html>
<html lang="en">
<head>
<meta charset="utf-8">
<title>Marlowe Group – Business Card</title>
<link href="https://fonts.googleapis.com/css2?family=Open+Sans:wght@400;700&display=swap" rel="stylesheet">
<style>
  :root {
    --stage: #2e2824;
    --card: #111214;
    --card-edge: #1b1c1f;
    --ink: #f2f2f2;
    --ink-soft: #dcdcdc;
    --rule: #bfbfbf;
  }
  * { margin: 0; padding: 0; box-sizing: border-box; }
  html, body {
    width: 1200px;
    height: 769px;
    overflow: hidden;
    background: var(--stage);
    font-family: "Open Sans", sans-serif;
  }
  .stage {
    width: 1200px;
    height: 769px;
    display: flex;
    align-items: center;
    justify-content: center;
    gap: 60px;
  }
  .card {
    position: relative;
    width: 510px;
    height: 312px;
    background: var(--card);
    border: 1px solid var(--card-edge);
    border-radius: 3px;
    box-shadow: 0 18px 40px rgba(0, 0, 0, 0.45);
  }
  /* Details side */
  .contact {
    position: absolute;
    right: 60px;
    top: 118px;
    width: 240px;
    text-align: center;
    color: var(--ink-soft);
  }
  .contact__name {
    font-weight: 700;
    font-size: 18px;
    letter-spacing: 1px;
    color: var(--ink);
    text-align: right;
    text-transform: uppercase;
    padding-bottom: 4px;
    border-bottom: 1px solid var(--rule);
  }
  .contact__line {
    font-size: 14.5px;
    line-height: 20px;
  }
  .contact__line:first-of-type { margin-top: 4px; }
  /* Name side */
  .card--name {
    display: flex;
    align-items: flex-start;
    justify-content: center;
  }
  .company-name {
    margin-top: 92px;
    margin-left: 90px;
    font-weight: 400;
    font-size: 26px;
    letter-spacing: 1px;
    color: var(--ink-soft);
  }
</style>
</head>
<body>
  <main class="stage">
    <section class="card card--details" aria-label="Contact side">
      <div class="contact">
        <h1 class="contact__name">Daniel Marlowe</h1>
        <p class="contact__line">0413586207</p>
        <p class="contact__line">danmarl@inboxmail.test</p>
        <p class="contact__line">www.marlowegroup.test</p>
      </div>
    </section>
    <section class="card card--name" aria-label="Company side">
      <span class="company-name">Marlowe Group</span>
    </section>
  </main>
</body>
</html>
```